QRV Advisors needs a web site

We need a web site for www.qrvadvisors-example.com. QRV is a mergers and acquisition consulting company that focuses our buyer and seller services on logistics companies. We help put companies together, and help with legal and financial due diligence. We want the web site to express our service and show the logistics components. We want personalized images versus pictures of trucks and airplanes.

Our new logo uses Burgandy and grey colors. Image attached. We are not in to bold, big letters...classy, artistic, low key preferred. Confidentiality, experience, professional are what we want to express on the site.

All we expect for the first part of this project is a home page, and one subpage.  We are budgeting other funds for the technical aspects of the web site

Reason: All that I'm seeing so far is trucks, forklifts and planes. We are a legal mergers and acquisitions firm that focus on logistics. I like some of the images to say logistics, but really want it say legal, financial, and putting companies together. Will pay extra for the sub page if someone can impress us with a home page.

Reason: Swamped with another project at the moment...will work on this over the weekend and provide designer feedback and select final design by Tuesday

```html
<!DOCTYPE html>
<html lang="en">
<head>
<meta charset="utf-8">
<title>QRV Advisors — Home</title>
<link href="https://fonts.googleapis.com/css2?family=Lato:wght@400;700&family=Cinzel:wght@400;700&family=Oswald:wght@400&display=swap" rel="stylesheet">
<style>
:root{
  --burgundy:#a50c30;
  --burgundy-dark:#7c0a24;
  --ink:#2b2b2b;
  --text:#444;
  --muted:#777;
  --line:#dcdcdc;
  --footer:#262626;
  --white:#fff;
}
*{box-sizing:border-box;margin:0;padding:0}
html,body{width:962px;height:1200px;overflow:hidden}
body{position:relative;font-family:'Lato',sans-serif;color:var(--text);background:#fbfbfb}
.abs{position:absolute}

/* header */
.site-header{position:absolute;left:0;top:0;width:962px;height:91px;background:linear-gradient(#fdfdfd,#ececec);border-bottom:1px solid #cfcfcf}
.brand{left:108px;top:26px;display:flex;align-items:center;gap:10px}
.brand-mark{width:16px;height:16px;background:var(--burgundy)}
.brand-name{font-family:'Lato',sans-serif;font-size:26px;font-weight:400;color:#555;letter-spacing:1px}
.phone{right:106px;top:15px;font-size:13px;color:#444;display:flex;align-items:center;gap:5px}
.main-nav{right:106px;top:63px;display:flex;align-items:center;font-size:12.5px;color:#333}
.main-nav a{color:inherit;text-decoration:none;padding:0 12px;border-left:1px solid #ddd;line-height:18px}
.main-nav a:first-child{border:none}
.main-nav a.active{background:var(--burgundy);color:#fff;font-weight:700;padding:0 7px;border-radius:2px;margin-right:6px}

/* hero */
.hero{left:0;top:92px;width:962px;height:359px;background:linear-gradient(180deg,#c9c9c9 0%,#a9a9a9 45%,#d2d2d2 100%)}
.slider-frame{left:105px;top:113px;width:751px;height:292px;background:#fff;box-shadow:0 2px 6px rgba(0,0,0,.3)}
.slide-photo{left:109px;top:117px;width:744px;height:284px;background:linear-gradient(100deg,#b9c6d4 0%,#e6e1dc 35%,#8b97a6 60%,#cfd6de 100%)}
.slide-caption{left:495px;top:280px;width:358px;height:85px;background:rgba(0,0,0,.85);color:#fff;font-family:'Cinzel',serif;font-size:20px;line-height:26px;text-align:center;padding-top:5px;letter-spacing:.5px}
.slider-tab{left:425px;top:404px;width:110px;height:28px}

/* services */
.service{width:190px;text-align:center}
.service-icon{width:86px;height:86px;border-radius:50%;border:1px solid #ccc;background:#fff;margin:0 auto;display:flex;align-items:center;justify-content:center}
.service-icon.active{background:var(--burgundy);border-color:var(--burgundy)}
.service h3{font-weight:400;font-size:15.5px;color:#222;margin-top:9px}
.service p{font-size:11.5px;line-height:15px;color:#444;margin-top:5px}
.btn{display:inline-block;background:var(--burgundy);color:#fff;font-size:11.5px;font-weight:700;padding:2px 7px;border-radius:1px;margin-top:10px}
.email-field{width:166px;height:22px;border:1px solid #ccc;background:#fff;margin:6px auto 0;font-size:10.5px;color:#999;text-align:left;padding:4px 7px}
.divider{left:108px;top:693px;width:748px;height:1px;background:linear-gradient(90deg,transparent,#ddd,transparent)}

/* panels */
.panel{width:236px;height:228px;background:#fff;border:1px solid #e2e2e2;box-shadow:0 6px 6px -4px rgba(0,0,0,.25)}
.panel-head{position:absolute;left:-5px;top:10px;width:246px;height:31px;background:linear-gradient(90deg,#111,#333);color:#fff;font-family:'Cinzel',serif;font-size:15.5px;letter-spacing:1px;padding:7px 10px}
.panel-badge{position:absolute;right:8px;top:2px;width:27px;height:27px;border-radius:50%;background:#fff;display:flex;align-items:center;justify-content:center}
.panel-badge i{width:19px;height:19px;border-radius:50%;background:var(--burgundy);display:block}
.more{position:absolute;right:14px;bottom:14px;font-size:10.5px;font-weight:700;color:var(--burgundy)}
.team-photo{position:absolute;left:13px;top:54px;width:208px;height:86px;background:linear-gradient(90deg,#c7cdd3,#9aa5b0,#d7d3cf)}
.panel-text{position:absolute;left:12px;top:150px;width:214px;font-size:10.5px;line-height:16px;color:#444}
.news-item{position:absolute;left:13px;width:210px;display:flex;gap:5px;padding-bottom:4px;border-bottom:1px solid #eee}
.date{width:29px;flex:none;text-align:center;font-weight:700;color:#fff}
.date b{display:block;background:var(--burgundy);font-size:11px;line-height:15px}
.date span{display:block;background:#777;font-size:8px;line-height:10px}
.news-item p{font-size:10.3px;line-height:14px;color:#444}
.news-item strong{color:#222}
.avatar{position:absolute;left:10px;top:60px;width:70px;height:70px;border-radius:50%;border:2px solid #ddd;background:linear-gradient(#c7b8ae,#6d7480)}
.quote{position:absolute;left:90px;top:60px;width:138px;font-size:10.3px;line-height:16px;color:#444}
.quote strong{color:#222}
.quote-body{position:absolute;left:10px;top:150px;width:216px;font-size:10.3px;line-height:16px}
.quote-by{position:absolute;left:10px;top:178px;font-size:10.3px;font-weight:700;color:#222}

/* footer */
.footer-wave{left:0;top:910px;width:962px;height:290px}
.footer-links{font-size:11px;color:#fff;line-height:22px;list-style:none}
.footer-links li::before{content:"•";color:#888;margin-right:5px;font-size:8px}
.map{left:384px;top:1084px;width:190px;height:70px;border:2px solid #999;background:linear-gradient(135deg,#e9e2d2,#f2c27f 50%,#cfe0ec)}
.address{left:382px;top:1160px;font-size:10.5px;line-height:13px;color:#fff;display:flex;gap:6px}
.cta{left:623px;top:1060px;font-family:'Oswald',sans-serif;color:#fff;font-size:14px;line-height:24px}
.appt{display:inline-block;background:linear-gradient(#fff,#ddd);color:#222;padding:0 7px;margin-left:4px;border-radius:2px;line-height:20px}
.social{left:683px;top:1130px;display:flex;gap:9px}
.social i{width:19px;height:19px;border-radius:50%;background:#d8d8d8;display:block}
.copyright{left:650px;top:1176px;font-size:9.5px;color:#ddd}
</style>
</head>
<body>

<header class="site-header">
  <div class="abs brand"><span class="brand-mark"></span><span class="brand-name">QRV Advisors</span></div>
  <div class="abs phone">
    <svg width="12" height="12" viewBox="0 0 24 24"><path fill="#a50c30" d="M6.6 10.8a15 15 0 006.6 6.6l2.2-2.2c.3-.3.7-.4 1-.2 1.1.4 2.3.6 3.6.6.6 0 1 .4 1 1V20c0 .6-.4 1-1 1C10.6 21 3 13.4 3 4c0-.6.4-1 1-1h3.5c.6 0 1 .4 1 1 0 1.3.2 2.5.6 3.6.1.3 0 .7-.2 1z"/></svg>
    123 456 7890
  </div>
  <nav class="abs main-nav">
    <a class="active">Home</a><a>About</a><a>Consulting Services</a><a>News &amp; Events</a><a>FAQ's</a><a>Contact</a>
  </nav>
</header>

<section class="abs hero" role="img" aria-label="Faded backdrop of a loading port with trucks and containers"></section>
<div class="abs slider-frame"></div>
<div class="abs slide-photo" role="img" aria-label="Photo of business people in a meeting"></div>
<div class="abs slide-caption">We are a legal mergers<br>and acquisitions firm that<br>focus on logistics.</div>
<svg class="abs slider-tab" viewBox="0 0 110 28">
  <path d="M0 0H110L98 22Q95 28 88 28H22Q15 28 12 22Z" fill="#f2f2f2"/>
  <circle cx="29" cy="12" r="4.5" fill="#a50c30"/><circle cx="47" cy="12" r="4.5" fill="#777"/>
  <circle cx="65" cy="12" r="4.5" fill="#777"/><circle cx="83" cy="12" r="4.5" fill="#777"/>
</svg>

<section>
  <div class="abs service" style="left:101px;top:481px">
    <div class="service-icon active"><svg width="44" height="40" viewBox="0 0 44 40"><rect x="2" y="4" width="30" height="30" rx="3" fill="#fff"/><rect x="6" y="12" width="22" height="18" fill="#a50c30"/><g fill="#fff"><rect x="8" y="14" width="4" height="4"/><rect x="14" y="14" width="4" height="4"/><rect x="20" y="14" width="4" height="4"/><rect x="8" y="20" width="4" height="4"/><rect x="14" y="20" width="4" height="4"/></g><circle cx="32" cy="28" r="10" fill="#fff"/><path d="M32 21v7h5" stroke="#a50c30" stroke-width="2" fill="none"/></svg></div>
    <h3>Business Planning</h3>
    <p>Lorem ipsum dolor sit amet,<br>consect ectetuer adipiscing elit,<br>sed diamgra nonummy.</p>
    <span class="btn">Read More</span>
  </div>
  <div class="abs service" style="left:282px;top:481px">
    <div class="service-icon"><svg width="46" height="40" viewBox="0 0 46 40"><circle cx="28" cy="8" r="7" fill="#222"/><path d="M14 34q0-17 14-17t14 17z" fill="#222"/><rect x="4" y="20" width="24" height="16" fill="#fff" stroke="#222" stroke-width="2.5"/><g fill="#222"><rect x="9" y="27" width="2" height="6"/><rect x="13" y="25" width="2" height="8"/><rect x="17" y="28" width="2" height="5"/><rect x="21" y="24" width="2" height="9"/></g></svg></div>
    <h3>Business Merger</h3>
    <p>Lorem ipsum dolor sit amet,<br>consect ectetuer adipiscing elit,<br>sed diamgra nonummy.</p>
    <span class="btn">Read More</span>
  </div>
  <div class="abs service" style="left:476px;top:481px;width:190px">
    <div class="service-icon"><svg width="40" height="44" viewBox="0 0 40 44"><rect x="5" y="2" width="30" height="20" fill="none" stroke="#222" stroke-width="2.5"/><circle cx="14" cy="10" r="2.5" fill="#222"/><rect x="12" y="13" width="4" height="9" fill="#222"/><g fill="#222"><rect x="22" y="13" width="2" height="5"/><rect x="26" y="10" width="2" height="8"/><rect x="30" y="7" width="2" height="11"/></g><g fill="#222"><circle cx="8" cy="30" r="4"/><circle cx="20" cy="30" r="4"/><circle cx="32" cy="30" r="4"/><path d="M2 42q0-8 6-8t6 8zM14 42q0-8 6-8t6 8zM26 42q0-8 6-8t6 8z"/></g></svg></div>
    <h3>Acquisition (M&amp;A) Advisory</h3>
    <p>Lorem ipsum dolor sit amet,<br>consect ectetuer adipiscing elit,<br>sed diamgra nonummy.</p>
    <span class="btn">Read More</span>
  </div>
  <div class="abs service" style="left:670px;top:481px">
    <div class="service-icon"><svg width="44" height="30" viewBox="0 0 44 30"><rect x="1" y="1" width="42" height="28" fill="#222"/><path d="M3 3l19 15 19-15M3 27l14-13M41 27L27 14" stroke="#fff" stroke-width="2" fill="none"/></svg></div>
    <h3>Newsletter Signup</h3>
    <div class="email-field">Enter your email here</div>
    <p style="margin-top:10px">Signup for QRV Newsletter!</p>
    <span class="btn" style="margin-top:8px">Subscribe</span>
  </div>
</section>
<div class="abs divider"></div>

<article class="abs panel" style="left:108px;top:720px">
  <div class="panel-head">What we do<span class="panel-badge"><i></i></span></div>
  <div class="team-photo" role="img" aria-label="Photo of a team of business colleagues"></div>
  <p class="panel-text">QRV can help you formulate and execute your growth strategy. We take a strategic and consultative approach...</p>
  <span class="more">Read More</span>
</article>

<article class="abs panel" style="left:365px;top:720px">
  <div class="panel-head">News &amp; Events<span class="panel-badge"><i></i></span></div>
  <div class="news-item" style="top:54px"><div class="date"><b>22</b><span>JULY</span></div><p><strong>Duis aute irure dolor in repre</strong><br>Duis autem vel eum iriure dolor inbo dolor hendrerit in amet vulputate.</p></div>
  <div class="news-item" style="top:104px"><div class="date"><b>22</b><span>JULY</span></div><p><strong>Duis aute irure dolor in repre</strong><br>Duis autem vel eum iriure dolor inbo dolor hendrerit in amet vulputate.</p></div>
  <div class="news-item" style="top:153px;border:none"><div class="date"><b>22</b><span>JULY</span></div><p><strong>Duis aute irure dolor in repre</strong><br>Duis autem vel eum iriure dolor inbo dolor hendrerit in amet vulputate.</p></div>
  <span class="more">Read More</span>
</article>

<article class="abs panel" style="left:621px;top:720px">
  <div class="panel-head">Client Testimonials<span class="panel-badge"><i></i></span></div>
  <div class="avatar" role="img" aria-label="Client portrait"></div>
  <p class="quote"><strong>“ Lorem ipsum dolor sita</strong><br>Sed diam nonummy euismli tincidunt laorlpi dolore smit aliquam erat volutpat.</p>
  <p class="quote-body">Duis autem vel eum iriure dolor in dolor hend sit in amet sit vulputate velit uisam.</p>
  <p class="quote-by">- Mr. Client Name</p>
  <span class="more">Read More</span>
</article>

<svg class="abs footer-wave" viewBox="0 0 962 290" preserveAspectRatio="none">
  <defs>
    <linearGradient id="dark" x1="0" y1="0" x2="0" y2="1"><stop offset="0" stop-color="#4a4a4a"/><stop offset="0.4" stop-color="#2a2a2a"/><stop offset="1" stop-color="#1c1c1c"/></linearGradient>
    <linearGradient id="wine" x1="0" y1="0" x2="1" y2="0"><stop offset="0" stop-color="#6d0a20"/><stop offset="0.3" stop-color="#b10f36"/><stop offset="1" stop-color="#7a0a25"/></linearGradient>
  </defs>
  <path d="M0 10Q120 120 380 120T962 70V290H0Z" fill="#bdbdbd"/>
  <path d="M0 10Q120 110 380 110T962 60V290H0Z" fill="url(#wine)"/>
  <path d="M0 50Q160 150 400 145T962 88V290H0Z" fill="#e4e4e4"/>
  <path d="M0 72Q180 170 410 160T962 98V290H0Z" fill="url(#dark)"/>
</svg>

<footer>
  <ul class="abs footer-links" style="left:113px;top:1111px"><li>Home</li><li>About</li><li>Consulting Services</li></ul>
  <ul class="abs footer-links" style="left:233px;top:1111px"><li>News &amp; Events</li><li>FAQ's</li><li>Contact</li></ul>
  <div class="abs map" role="img" aria-label="Street map of the Chicago office area"></div>
  <div class="abs address">
    <svg width="14" height="20" viewBox="0 0 14 20"><path d="M7 0a7 7 0 00-7 7c0 5 7 13 7 13s7-8 7-13a7 7 0 00-7-7z" fill="#fff"/><circle cx="7" cy="7" r="2.6" fill="#262626"/></svg>
    <span>QRV Advisors<br>Sanfransisco, Miami, Chicago.</span>
  </div>
  <div class="abs cta">Schedule Free Consultation <span class="appt">Appointment</span><br>Or Call Us on : (123) 456 7890</div>
  <div class="abs social" aria-label="Social links"><i></i><i></i><i></i><i></i></div>
  <p class="abs copyright">© Copyright 2013 QRV Advisors.</p>
</footer>

</body>
</html>
```